The logo name is "Harbor Skin". The name of the product will be "Cutaneous Comfort". This product is specifically formulated for amputees. Therefore under the product name it should state "for amputees". The catch phrase will be "Experience Harbor find Calmness"
These are the things we need on the label:
Logo, product name, "for amputees", "Experience Harbor find Calmness", Safe, Effective, Directions: spray on problem areas, no need to dry off. harborskin.example, Made in Canada, 500ml.
The MOST IMPORTANT and therefore the most prominent thing on this lable will be the LOGO! The second most prominent thing will be the word "Comfort" We want to keep it very plain, very simple, very unclutered. Keep in mind that this lable will be placed on a white bottle or have a white back ground. The 500ml white PE bottle with trigger sprayer will have a tear drop label. See attached die line (S-294).
We want to stay with the colours that goes with the colour scheme of the logo. See attached logo. Soft colours. We do not want a picture! We would like the lable to be classy and rich.
Updates
The logo name is "Harbor Skin". The name of the product will be "Cutaneous Comfort". This product is specificlly formulated for amputees. Therefore under the product name it should state "for amputees". The catch phrase will be "Experience Harbor find Calmness"
Logo, product name, "for amputees", catch phrase "Experience Harbor find Calmness", Clean, Safe, Effective, Directions: spray on problem areas, no need to dry off. Also Harbor Skin Corpation, harborskin.example, Made in Canada, 500ml.
We want to stay with the colour scheme of the logo. See attached logo. Soft colours. We do not want a picture! We would like the lable to be classy and rich.
This is the offical directive that came from the governing panal of this lable. This panal it not know where it wanted to take this lable that would represent this line until they review all of your submissions, thank you for all your talented hard work. But now it is clear it is time to regroup and hit this objective.
Project Deadline Extended
Reason: New restrictions on lable wording for this product.
Target Market(s)
Amputees and Parents of.
Industry/Entity Type
Product
Requirements
Must have
- Final product to be in a pdf or an illustrator file

```html
<!DOCTYPE html>
<html lang="en">
<head>
<meta charset="utf-8">
<title>Cutaneous Comfort – Teardrop Label Concepts</title>
<link href="https://fonts.googleapis.com/css2?family=Ubuntu:wght@400;500&display=swap" rel="stylesheet">
<style>
  :root {
    --page-bg: #ffffff;
    --teal-deep: #0fb0ab;
    --teal-mid: #1aa9a6;
    --teal-soft: #7fcfcc;
    --teal-muted: #5dbdb9;
    --sky: #92daf0;
    --label-grey: #e2e8e9;
    --label-white: #f9fbfc;
    --ink-white: #ffffff;
  }
  html, body {
    margin: 0;
    padding: 0;
    width: 1200px;
    height: 900px;
    overflow: hidden;
    background: var(--page-bg);
  }
  .artboard { width: 1200px; height: 900px; display: block; }
  .label-text {
    font-family: "Ubuntu", "Trebuchet MS", sans-serif;
    text-anchor: middle;
  }
  .brand-name {
    font-family: "Ubuntu", "Trebuchet MS", sans-serif;
    font-weight: 500;
    font-size: 30px;
  }
  .product-line { font-size: 20px; }
  .product-key { font-size: 44px; }
  .audience { font-size: 19px; }
  .catch-phrase { font-size: 14px; }
  .claims { font-size: 14px; font-weight: 500; }
  .directions { font-size: 12px; }
  .footer-line { font-size: 11px; }

  .label--soft .tone { fill: var(--teal-soft); }
  .label--soft .tone-muted { fill: var(--teal-muted); }
  .label--soft .brand-name { fill: var(--teal-deep); }
  .label--soft .brand-square { fill: var(--teal-deep); }

  .label--rich .tone { fill: var(--teal-mid); }
  .label--rich .tone-muted { fill: var(--teal-mid); }
  .label--rich .brand-name { fill: var(--teal-mid); }
  .label--rich .brand-square { fill: var(--teal-mid); }

  .badge-text { fill: var(--ink-white); font-size: 18px; }
  .badge-text--small { fill: var(--ink-white); font-size: 14.5px; }
</style>
</head>
<body>
<svg class="artboard" viewBox="0 0 1024 768" xmlns="http://www.w3.org/2000/svg" aria-label="Two teardrop label concepts for Cutaneous Comfort by Harbor Skin">
  <defs>
    <linearGradient id="label-fill" x1="0" y1="0" x2="1" y2="0">
      <stop offset="0" stop-color="var(--label-grey)"/>
      <stop offset="1" stop-color="var(--label-white)"/>
    </linearGradient>
    <linearGradient id="rim-stroke" x1="0" y1="0" x2="1" y2="0">
      <stop offset="0.35" stop-color="var(--teal-deep)"/>
      <stop offset="1" stop-color="var(--sky)"/>
    </linearGradient>
    <linearGradient id="badge-fill" x1="0" y1="0" x2="1" y2="0">
      <stop offset="0" stop-color="var(--teal-deep)"/>
      <stop offset="1" stop-color="#6fcfd9"/>
    </linearGradient>
    <path id="teardrop" d="M222 92 Q232 84 246 93 C330 170 432 320 456 470 Q470 560 460 620 Q455 646 428 646 L180 646 Q152 646 150 616 Q141 480 160 360 C180 230 200 140 222 92 Z"/>
    <clipPath id="right-label-clip">
      <use href="#teardrop" transform="translate(400 0)"/>
    </clipPath>
  </defs>

  <!-- Concept one: soft tones with square badge -->
  <g class="label label--soft">
    <use href="#teardrop" fill="url(#label-fill)" stroke="url(#rim-stroke)" stroke-width="5"/>
    <rect class="brand-square" x="194" y="278" width="22" height="22"/>
    <text class="brand-name" x="224" y="300">Harbor Skin</text>
    <text class="label-text product-line tone" x="292" y="345">Cutaneous</text>
    <text class="label-text product-key tone" x="292" y="390">Comfort</text>
    <text class="label-text audience tone" x="292" y="415">for amputees</text>
    <text class="label-text catch-phrase tone-muted" x="300" y="445">Experience Harbor find Calmness</text>
    <text class="label-text claims tone-muted" x="302" y="474">Clean · Safe · Effective</text>
    <text class="label-text directions tone-muted" x="304" y="502">Directions: spray on problem areas,</text>
    <text class="label-text directions tone-muted" x="304" y="518">no need to dry off.</text>
    <text class="label-text footer-line tone-muted" x="304" y="543">Harbor Skin Corpation · harborskin.example</text>
    <text class="label-text footer-line tone-muted" x="304" y="558">Made in Canada · 500ml</text>
    <rect class="badge badge--square" x="244" y="569" width="108" height="74" fill="url(#badge-fill)"/>
    <text class="label-text badge-text" x="298" y="600">Naturally</text>
    <text class="label-text badge-text" x="298" y="623">Hygienic</text>
  </g>

  <!-- Concept two: rich tones with round badge -->
  <g class="label label--rich">
    <use href="#teardrop" transform="translate(400 0)" fill="url(#label-fill)" stroke="url(#rim-stroke)" stroke-width="5"/>
    <g clip-path="url(#right-label-clip)">
      <circle class="badge badge--round" cx="601" cy="603" r="46" fill="var(--teal-deep)"/>
    </g>
    <rect class="brand-square" x="594" y="278" width="22" height="22"/>
    <text class="brand-name" x="624" y="300">Harbor Skin</text>
    <text class="label-text product-line tone" x="692" y="345">Cutaneous</text>
    <text class="label-text product-key tone" x="692" y="390">Comfort</text>
    <text class="label-text audience tone" x="692" y="415">for amputees</text>
    <text class="label-text catch-phrase tone-muted" x="700" y="445">Experience Harbor find Calmness</text>
    <text class="label-text claims tone-muted" x="702" y="474">Clean · Safe · Effective</text>
    <text class="label-text directions tone-muted" x="704" y="502">Directions: spray on problem areas,</text>
    <text class="label-text directions tone-muted" x="704" y="518">no need to dry off.</text>
    <text class="label-text footer-line tone-muted" x="704" y="543">Harbor Skin Corpation · harborskin.example</text>
    <text class="label-text footer-line tone-muted" x="704" y="558">Made in Canada · 500ml</text>
    <text class="label-text badge-text--small" x="601" y="600">Naturally</text>
    <text class="label-text badge-text--small" x="601" y="618">Hygienic</text>
  </g>
</svg>
</body>
</html>
```